Classy, Elegant, Simple Business Card Design

Looking to have a classy, simple, and elegant design. Want a top notch designed business card. I really like the look of the new torvane credit card. I also like the design I attached. I am trying to reach 21-29 year old females for booking us for there wedding or event. We offer Disc Jockey Service, Photo Booth Rentals, and Uplighting .

Target Market(s)

21-28 year old females

Contact Information for Business Card

Has to have logo, website, email, and phone number

Font styles to use
Other font styles liked:
• open to font choice, modern, clean
Designer to choose
33a6d7
0791cd
0555a3
ffffff

Requirements
Must have
• Has to have logo, website, email, and phone number
Nice to have
• I really like the design of the new torvane credit card. I also included my logo and some designs I like
Should not have
• clutter or too much info

```html
<!DOCTYPE html>
<html lang="en">
<head>
<meta charset="utf-8">
<title>Lumen Tide Event Group – Business Card</title>
<link href="https://fonts.googleapis.com/css2?family=Montserrat:wght@400;600&family=Roboto:wght@400&display=swap" rel="stylesheet">
<style>
  :root {
    --page-bg: #dcd6cf;
    --card-light: #f1f3f5;
    --card-light-2: #e2e6ea;
    --panel-blue: #1d5a8e;
    --panel-blue-deep: #164a78;
    --curve-edge: #111a24;
    --brand-blue: #0555a3;
    --accent-gold: #e6d4b2;
    --contact-text: #dcdcd8;
    --icon-tint: #d6c7a8;
  }
  * { margin: 0; padding: 0; box-sizing: border-box; }
  html, body {
    width: 1200px; height: 1054px; overflow: hidden;
    background: var(--page-bg);
  }
  .card {
    position: absolute; left: 120px; top: 247px;
    width: 960px; height: 560px;
    box-shadow: 0 18px 40px rgba(0,0,0,0.18);
    overflow: hidden;
  }
  .card-shape { position: absolute; inset: 0; }
  .brand {
    position: absolute; left: 40px; top: 300px; width: 380px;
    text-align: center;
    font-family: "Montserrat", sans-serif; font-weight: 600;
    color: var(--brand-blue);
  }
  .brand-name { font-size: 40px; letter-spacing: 2px; line-height: 1.1; }
  .brand-tag { font-size: 17px; letter-spacing: 8px; margin-top: 8px; text-transform: uppercase; }
  .person { position: absolute; left: 581px; top: 172px; }
  .person-name {
    font-family: "Montserrat", sans-serif; font-weight: 600;
    font-size: 38px; color: var(--accent-gold);
  }
  .person-role {
    font-family: "Roboto", sans-serif; font-size: 23px;
    color: var(--accent-gold); margin-top: 6px;
  }
  .contacts { position: absolute; left: 581px; top: 290px; list-style: none; }
  .contacts li {
    display: flex; align-items: center; height: 37px;
    font-family: "Roboto", sans-serif; font-size: 23px; color: var(--contact-text);
  }
  .contacts svg { width: 22px; height: 22px; margin-right: 22px; flex: none; }
</style>
</head>
<body>
  <div class="card">
    <svg class="card-shape" viewBox="0 0 960 560" width="960" height="560">
      <defs>
        <linearGradient id="lightSide" x1="0" y1="0" x2="1" y2="1">
          <stop offset="0" stop-color="var(--card-light)"/>
          <stop offset="1" stop-color="var(--card-light-2)"/>
        </linearGradient>
        <linearGradient id="blueSide" x1="0" y1="0" x2="1" y2="1">
          <stop offset="0" stop-color="var(--panel-blue)"/>
          <stop offset="1" stop-color="var(--panel-blue-deep)"/>
        </linearGradient>
      </defs>
      <rect class="card-base" width="960" height="560" fill="url(#lightSide)"/>
      <path class="curve-edge" d="M428,0 Q562,280 418,560 L436,560 Q574,280 444,0 Z" fill="var(--curve-edge)"/>
      <path class="info-panel" d="M444,0 Q574,280 436,560 L960,560 L960,0 Z" fill="url(#blueSide)"/>
    </svg>

    <div class="brand">
      <div class="brand-name">LUMEN TIDE</div>
      <div class="brand-tag">Event Group</div>
    </div>

    <div class="person">
      <div class="person-name">Evan Hartley</div>
      <div class="person-role">Founder &amp; CEO</div>
    </div>

    <ul class="contacts">
      <li>
        <svg viewBox="0 0 24 24" aria-hidden="true"><path fill="var(--icon-tint)" d="M3 8c0-2 4-4 9-4s9 2 9 4v2h-5V8H8v2H3z M6 11h12l2 8H4z"/></svg>
        555 0142 0199
      </li>
      <li>
        <svg viewBox="0 0 24 24" aria-hidden="true"><rect x="2" y="5" width="20" height="14" fill="var(--icon-tint)"/><path d="M2 5l10 8 10-8" fill="none" stroke="var(--panel-blue)" stroke-width="2"/></svg>
        evan@lumentide.com
      </li>
      <li>
        <svg viewBox="0 0 24 24" aria-hidden="true"><g fill="none" stroke="var(--icon-tint)" stroke-width="2"><circle cx="12" cy="12" r="9"/><ellipse cx="12" cy="12" rx="4" ry="9"/><path d="M3 12h18"/></g></svg>
        www.lumentide.com
      </li>
    </ul>
  </div>
</body>
</html>
```